MRT Property - Business Cards

Looking for a business card & general letterhead, signage etc design for our new logo.

Colours:
000a20
0056a2
00b5ef
0088ce
68cef2

Fonts:
Poppins
Karla

Please keep look and feel of new brand - example in the zip package I sent.

```html
<!DOCTYPE html>
<html lang="en">
<head>
<meta charset="utf-8">
<title>MRT Property – Business Card</title>
<link rel="stylesheet" href="https://fonts.googleapis.com/css2?family=Poppins:wght@400;500;600&display=swap">
<style>
  :root {
    --navy-deep: #000a20;
    --card-dark: #0f1424;
    --blue-brand: #0056a2;
    --blue-mid: #0088ce;
    --blue-bright: #2aa9e3;
    --blue-light: #68cef2;
    --rule: #4f7fb3;
    --ink: #3a3a3a;
    --ink-soft: #555;
    --paper: #ffffff;
    --backdrop: #e8e5e0;
  }
  * { margin: 0; padding: 0; box-sizing: border-box; }
  html, body { width: 900px; height: 1200px; overflow: hidden; }
  body {
    background: var(--backdrop);
    font-family: "Poppins", sans-serif;
    position: relative;
  }
  .card {
    position: absolute;
    left: 80px;
    width: 742px;
    height: 440px;
    border-radius: 30px;
    box-shadow: 0 4px 10px rgba(0,0,0,0.18);
    overflow: hidden;
  }
  .card--front { top: 132px; background: var(--paper); }
  .card--back { top: 638px; background: var(--card-dark); }

  .wordmark {
    position: absolute;
    display: flex;
    align-items: center;
    font-weight: 600;
    white-space: nowrap;
    line-height: 1.2;
  }
  .wordmark__dot { border-radius: 50%; flex: none; }
  .card--front .wordmark { left: 38px; top: 58px; gap: 14px; font-size: 42px; color: var(--blue-brand); }
  .card--front .wordmark__dot { width: 46px; height: 46px; background: var(--blue-bright); }
  .card--back .wordmark { left: 88px; top: 166px; gap: 22px; font-size: 64px; color: var(--blue-mid); }
  .card--back .wordmark__dot { width: 80px; height: 80px; background: var(--blue-light); }

  .holder { position: absolute; left: 37px; top: 276px; }
  .holder__name { font-size: 27px; font-weight: 600; color: var(--blue-bright); line-height: 1.1; }
  .holder__role { font-size: 15px; color: var(--ink-soft); margin-top: 2px; line-height: 1.2; }

  .divider {
    position: absolute; left: 37px; top: 334px;
    width: 672px; height: 1.5px; background: var(--rule);
  }

  .contacts { position: absolute; left: 37px; top: 346px; list-style: none; }
  .contacts li {
    display: flex; align-items: center; gap: 10px;
    font-size: 16px; color: var(--ink); height: 22px;
  }
  .contacts svg { width: 15px; height: 15px; fill: var(--blue-mid); flex: none; }

  .address {
    position: absolute; left: 475px; top: 366px;
    font-size: 16px; color: var(--ink); line-height: 22px; font-style: normal;
  }
</style>
</head>
<body>
  <section class="card card--front" aria-label="Business card front">
    <div class="wordmark"><span class="wordmark__dot"></span>MRT Property</div>

    <div class="holder">
      <p class="holder__name">Corin Halvorsen</p>
      <p class="holder__role">Owner</p>
    </div>

    <div class="divider"></div>

    <ul class="contacts">
      <li>
        <svg viewBox="0 0 16 16" aria-hidden="true"><path d="M2 5c0-2 2-3 6-3s6 1 6 3v1h-3V5H5v1H2zM4 7h8l2 6H2z"/></svg>
        215-555-0147
      </li>
      <li>
        <svg viewBox="0 0 16 16" aria-hidden="true"><path d="M1 3h14v1L8 9 1 4zM1 6l7 5 7-5v7H1z"/></svg>
        info@mrtproperty.com.au
      </li>
      <li>
        <svg viewBox="0 0 16 16" aria-hidden="true"><path d="M8 1a7 7 0 1 0 0 14A7 7 0 0 0 8 1zm0 2c1 0 2 2 2 5s-1 5-2 5-2-2-2-5 1-5 2-5zM2.5 7.2h11v1.6h-11z"/></svg>
        www.mrtproperty.com.au
      </li>
    </ul>

    <address class="address">
      48 Meridian Way, Suite 210<br>
      Lansdale, PA 19446
    </address>
  </section>

  <section class="card card--back" aria-label="Business card back">
    <div class="wordmark"><span class="wordmark__dot"></span>MRT Property</div>
  </section>
</body>
</html>
```